Velora Entertainment

Logo for business card design

Target Market(s)

potential film investors and screenwriters

Industry/Entity Type

Business

Contact Information for Business Card

as shown, website here is a placeholder position

Requirements
Must have
• great visual appeal
Nice to have
• harmony of colors; must evoke spirit of
• U.S.-China cooperation

```html
<!DOCTYPE html>
<html lang="en">
<head>
<meta charset="utf-8">
<title>Velora Entertainment – Business Card</title>
<link rel="stylesheet" href="https://fonts.googleapis.com/css2?family=Open+Sans:wght@400;600;700&display=swap">
<style>
  :root {
    --page-bg: #3b3b3b;
    --card-white: #ffffff;
    --band-grey: #9a9a9a;
    --accent-red: #e3101b;
    --accent-yellow: #ffd200;
    --accent-blue: #141c7a;
    --ink: #1a1a1a;
    --brand-ink: #141c7a;
  }
  * { box-sizing: border-box; margin: 0; padding: 0; }
  html, body {
    width: 1105px;
    height: 1200px;
    overflow: hidden;
    background: var(--page-bg);
    font-family: "Open Sans", Arial, sans-serif;
  }
  .business-card {
    position: absolute;
    left: 72px;
    top: 326px;
    width: 960px;
    height: 548px;
    background: var(--card-white);
    color: var(--ink);
  }
  .card-shapes {
    position: absolute;
    inset: 0;
    width: 100%;
    height: 100%;
  }
  .brand {
    position: absolute;
    left: 55px;
    top: 118px;
    display: flex;
    align-items: center;
    gap: 18px;
  }
  .brand-mark {
    width: 54px;
    height: 54px;
    background: var(--accent-red);
  }
  .brand-name {
    font-weight: 700;
    font-size: 38px;
    line-height: 1;
    color: var(--brand-ink);
    letter-spacing: 0.5px;
  }
  .holder {
    position: absolute;
    right: 57px;
    top: 298px;
    text-align: right;
  }
  .holder-name {
    font-weight: 600;
    font-size: 32px;
    line-height: 44px;
  }
  .holder-role {
    font-size: 26px;
    line-height: 36px;
  }
  .address {
    position: absolute;
    right: 57px;
    top: 405px;
    text-align: right;
    font-size: 24px;
    line-height: 36px;
  }
  .contacts {
    position: absolute;
    left: 55px;
    top: 403px;
    list-style: none;
    font-size: 24px;
    line-height: 37px;
  }
  .contacts li {
    display: flex;
    align-items: center;
    gap: 14px;
  }
  .contact-icon {
    width: 24px;
    height: 24px;
    fill: var(--ink);
    flex: none;
  }
</style>
</head>
<body>
  <main class="business-card">
    <svg class="card-shapes" viewBox="0 0 522 298" preserveAspectRatio="none" aria-hidden="true">
      <polygon class="stripe-red" points="0,172 100,172 92,186 0,186" fill="var(--accent-red)"/>
      <polygon class="stripe-yellow" points="104,172 192,172 184,186 96,186" fill="var(--accent-yellow)"/>
      <polygon class="stripe-blue" points="196,172 290,172 280,186 188,186" fill="var(--accent-blue)"/>
      <polygon class="info-band" points="306,164 522,164 522,298 0,298 0,189 283,189" fill="var(--band-grey)"/>
    </svg>

    <div class="brand">
      <span class="brand-mark"></span>
      <span class="brand-name">Velora Entertainment</span>
    </div>

    <div class="holder">
      <p class="holder-name">Daniel Reyes</p>
      <p class="holder-role">CEO/Founder</p>
    </div>

    <address class="address" style="font-style: normal;">
      <p>1420 Harbor View Road</p>
      <p>Portland, Oregon 97205</p>
      <p>www.velorafilm.com</p>
    </address>

    <ul class="contacts">
      <li>
        <svg class="contact-icon" viewBox="0 0 24 24" aria-hidden="true"><path d="M6.6 10.8a15.1 15.1 0 0 0 6.6 6.6l2.2-2.2a1 1 0 0 1 1-.25 11.4 11.4 0 0 0 3.6.57 1 1 0 0 1 1 1V20a1 1 0 0 1-1 1A17 17 0 0 1 3 4a1 1 0 0 1 1-1h3.5a1 1 0 0 1 1 1c0 1.25.2 2.45.57 3.57a1 1 0 0 1-.25 1z"/></svg>
        <span>555 214 7720</span>
      </li>
      <li>
        <svg class="contact-icon" viewBox="0 0 24 24" aria-hidden="true"><path d="M7 1h10a2 2 0 0 1 2 2v18a2 2 0 0 1-2 2H7a2 2 0 0 1-2-2V3a2 2 0 0 1 2-2zm0 3v14h10V4zm5 15.5a1.2 1.2 0 1 0 0 2.4 1.2 1.2 0 0 0 0-2.4z"/></svg>
        <span>555 390 1846</span>
      </li>
      <li>
        <svg class="contact-icon" viewBox="0 0 24 24" aria-hidden="true"><path d="M2 5h20v14H2zm2 2v.5l8 5 8-5V7zm0 2.8V17h16V9.8l-8 5z"/></svg>
        <span>hello@velorafilm.com</span>
      </li>
    </ul>
  </main>
</body>
</html>
```